Online class need a Chapter Template

Basically, I have two main document templates:

Template 1: Chapter unit or the abstract concept explanation.

There are 4 main chapters and each chapter is linked to a color:
(RED Color) : Learning Communities
(YELLOW Color): Exploring Online Learning Tools
(BLUE Color): Teaching and Learning Fundamentals
(GREEN Color): Online Teaching and Learning in Practice

Inside the chapter there are the same elements:
Learning Objectives
Introduction
Context
Concept Explanation
Activities (directions, challenge or task to perform)

Template 2: The tool guide and practical skill requirement

This one describes how to use an online tool
Updates

Good day everyone, I added a new file with the current template. I am using PageLoomMaker and really want to make this a little easier.

The project is about the Layout design of the Unit / Activity, and the layout proposal can be done in any tool

I really hope the new file helps explaining the concept (Sorry, English is not my primary language, but I will try my best)

Reason: Hi everyone, I am extending the deadline by 5 days to give the opportunity to the new invitees to submit their designs. I am looking forward to see your ideas! Kind regards, Tobias

Reason: Changed the project type in order to make it easier for designers to participate. Looking forward to your designs. Kind regards.

Reason: Waiting for a couple of designs re-submissions

Target Market(s)

The audience are online students 16-25 years old

Industry/Entity Type

Learning

Requirements
Must have
• For the Template 1 (Chapter) (see old sample attached)
The following elements are needed (each one with a graphic icon):
Learning Objectives
Introduction
Context
Concept Explanation

For the Template 2 (Tool) (see old sample attached)
Any creative idea is open here. This is basically the template to a small tutorial. The elements are:
Tool name and description
Where to find it (It contains the URL and QR Code)
Checklist template
Explanation Links
Tool Screenshots
Nice to have
• I am open to ideas. At the end, the main result will be five editable templates
4 chapter templates (sample named template 1) (RED, YELLOW, BLUE and GREEN)
1 Tool template (sample named template 2)

```html
<!DOCTYPE html>
<html lang="es">
<head>
<meta charset="utf-8">
<title>Comunidades Virtuales de Aprendizaje – Actividad 02</title>
<link rel="stylesheet" href="https://fonts.googleapis.com/css2?family=Zilla+Slab:ital,wght@0,300;0,400;1,300;1,400&display=swap">
<style>
  :root {
    --chapter-green: #3bb54a;
    --panel-grey: #f1f1f1;
    --badge-grey: #bcbdbf;
    --ring-grey: #c4c4c6;
    --ink: #222222;
    --body-ink: #555555;
    --white: #ffffff;
  }
  html, body {
    margin: 0;
    padding: 0;
    overflow: hidden;
    background: var(--white);
  }
  .page {
    position: relative;
    width: 848px;
    height: 1200px;
    overflow: hidden;
    background: var(--white);
    font-family: "Zilla Slab", Georgia, serif;
  }
  .chapter-header {
    position: absolute;
    left: 0; top: 0;
    width: 650px; height: 230px;
    background: var(--chapter-green);
  }
  .chapter-title {
    position: absolute;
    left: 24px; top: 50px;
    margin: 0;
    font-weight: 300;
    font-size: 53px;
    line-height: 65px;
    color: var(--white);
    letter-spacing: 0.5px;
  }
  .chapter-number-panel {
    position: absolute;
    left: 650px; top: 0;
    width: 198px; height: 230px;
    background: var(--panel-grey);
  }
  .chapter-number {
    position: absolute;
    left: 0; right: 0; top: 28px;
    text-align: center;
    font-weight: 300;
    font-size: 122px;
    line-height: 1;
    color: var(--chapter-green);
  }
  .activity-badge {
    position: absolute;
    left: 34px; top: 275px;
    width: 166px; height: 166px;
    border-radius: 50%;
    background: var(--badge-grey);
    display: flex;
    align-items: center;
    justify-content: center;
    text-align: center;
    font-style: italic;
    font-weight: 300;
    font-size: 32px;
    line-height: 37px;
    color: var(--ink);
  }
  .duration-ring {
    position: absolute;
    left: 214px; top: 276px;
    width: 170px; height: 170px;
  }
  .duration-label {
    position: absolute;
    left: 214px; top: 276px;
    width: 170px; height: 170px;
    display: flex;
    align-items: center;
    justify-content: center;
    text-align: center;
    font-style: italic;
    font-weight: 300;
    font-size: 31px;
    line-height: 36px;
    color: var(--chapter-green);
  }
  .activity-media {
    position: absolute;
    left: 24px; top: 470px;
    width: 803px; height: 318px;
    background: var(--panel-grey);
  }
  .activity-description {
    position: absolute;
    left: 33px; top: 809px;
    width: 791px;
    margin: 0;
    font-style: italic;
    font-weight: 300;
    font-size: 19.4px;
    line-height: 27px;
    text-align: justify;
    color: var(--body-ink);
  }
  .activity-points {
    position: absolute;
    left: 116px; top: 944px;
    margin: 0;
    padding: 0;
    list-style: none;
  }
  .activity-points li {
    position: relative;
    height: 60px;
    padding-left: 54px;
    font-style: italic;
    font-weight: 300;
    font-size: 20.5px;
    line-height: 36px;
    color: var(--ink);
  }
  .activity-points li::before {
    content: "";
    position: absolute;
    left: 0; top: 5px;
    width: 26px; height: 26px;
    border-radius: 50%;
    background: var(--chapter-green);
  }
  .page-footer {
    position: absolute;
    left: 0; top: 1128px;
    width: 650px; height: 72px;
    background: var(--chapter-green);
  }
  .page-number-panel {
    position: absolute;
    left: 650px; top: 1128px;
    width: 198px; height: 72px;
    background: var(--panel-grey);
    display: flex;
    align-items: center;
    justify-content: center;
    font-weight: 300;
    font-size: 34px;
    color: var(--chapter-green);
  }
</style>
</head>
<body>
  <main class="page">
    <header class="chapter-header">
      <h1 class="chapter-title">Comunidades Virtuales<br>de Aprendizaje</h1>
    </header>
    <div class="chapter-number-panel"><span class="chapter-number">01</span></div>

    <div class="activity-badge">activity<br>02</div>

    <svg class="duration-ring" viewBox="0 0 170 170" aria-hidden="true">
      <circle cx="85" cy="85" r="75" fill="none" stroke="var(--chapter-green)" stroke-width="13"
              stroke-dasharray="55.9 3" transform="rotate(-90 85 85)"/>
      <circle cx="85" cy="85" r="59" fill="none" stroke="var(--ring-grey)" stroke-width="7"/>
      <circle cx="85" cy="85" r="59" fill="none" stroke="var(--chapter-green)" stroke-width="7"
              stroke-dasharray="185.4 185.4" transform="rotate(-90 85 85)"/>
    </svg>
    <div class="duration-label">90<br>mins</div>

    <div class="activity-media" role="img" aria-label="Espacio para la imagen de la actividad"></div>

    <p class="activity-description">Lorem ipsum dolor sit amet, consectetur adipisicing elit, sed do eiusmod tempor incididunt ut labore et dolore magna aliqua. Ut enim ad minim veniam, quis nostrud exercitation ullamco laboris nisi ut aliquip ex ea commodo consequat. Duis aute</p>

    <ul class="activity-points">
      <li>Lorem ipsum dolor sit amet, consectetur adipisicing elit, sed do</li>
      <li>Lorem ipsum dolor sit amet, consectetur</li>
    </ul>

    <footer class="page-footer"></footer>
    <div class="page-number-panel">01</div>
  </main>
</body>
</html>
```